Professional & attention grabbing.

A business card design, front and back. I already have a logo I will attach, but I am open to something new as well.
Things to include:
Name:
Title:
Phone:
Email:
Wanting something that is professional but attention grabbing.
Also we do a lot of work using drones on natural gas pipelines (leading the future)if you want to include any of that. I'm open to ideas.
Target Market(s)
Natural gas transmission industry / greenhouse gas mitigation industry
Industry/Entity Type
Business
Colors
Designer to choose colors to be used in the design.
Look and feel
Each slider illustrates characteristics of the customer's brand and the style your logo design should communicate.

```html
<!DOCTYPE html>
<html lang="en">
<head>
<meta charset="UTF-8">
<title>Kestra Inspections – Business Card</title>
<link rel="stylesheet" href="https://fonts.googleapis.com/css2?family=Roboto:wght@400;500;700&family=Roboto+Condensed:wght@400;700&display=swap">
<style>
  :root {
    --bg: #e6e6e8;
    --card-dark: #2a2a2d;
    --card-dark-edge: #1c1c1e;
    --card-light: #ffffff;
    --red: #d71e1e;
    --red-dark: #a81515;
    --ink: #2b2b2e;
    --ink-soft: #444448;
    --white: #ffffff;
  }
  * { box-sizing: border-box; margin: 0; padding: 0; }
  html, body { width: 1200px; height: 852px; overflow: hidden; }
  body {
    background: var(--bg);
    font-family: "Roboto", Arial, sans-serif;
    position: relative;
  }
  .card {
    position: absolute;
    width: 525px;
    height: 300px;
    border-radius: 16px;
    overflow: hidden;
    box-shadow: 0 10px 26px rgba(0,0,0,.22);
  }

  /* Front */
  .card-front {
    left: 90px; top: 110px;
    background: linear-gradient(135deg, #38383c 0%, var(--card-dark) 50%, var(--card-dark-edge) 100%);
  }
  .card-front .brand {
    position: absolute;
    left: 0; right: 0; top: 98px;
    display: flex; align-items: center; justify-content: center; gap: 14px;
  }
  .brand-square { width: 30px; height: 30px; background: var(--red); }
  .card-front .brand-name {
    font-family: "Roboto Condensed", Arial, sans-serif;
    font-weight: 700; font-size: 40px; letter-spacing: 1px;
    color: var(--white); text-transform: uppercase;
  }
  .front-band {
    position: absolute; left: 0; right: 0; bottom: 30px;
    height: 38px;
    background: linear-gradient(180deg, var(--red) 0%, var(--red-dark) 100%);
    display: flex; align-items: center; justify-content: center;
  }
  .front-band p {
    color: var(--white); font-size: 16px; font-weight: 500; letter-spacing: .2px;
  }

  /* Back */
  .card-back {
    left: 585px; top: 440px;
    background: var(--card-light);
  }
  .card-back .brand {
    position: absolute; left: 36px; top: 48px;
    display: flex; align-items: center; gap: 10px;
  }
  .card-back .brand-square { width: 22px; height: 22px; }
  .card-back .brand-name {
    font-family: "Roboto Condensed", Arial, sans-serif;
    font-weight: 700; font-size: 28px; letter-spacing: .5px;
    color: var(--ink); text-transform: uppercase;
  }
  .person { position: absolute; left: 36px; top: 150px; }
  .person-name {
    font-weight: 700; font-size: 24px; letter-spacing: 1.5px;
    color: var(--red); text-transform: uppercase; line-height: 1;
  }
  .person-title { font-size: 14px; font-weight: 500; color: var(--ink-soft); margin-top: 4px; }
  .contacts { position: absolute; left: 36px; top: 212px; list-style: none; }
  .contacts li {
    display: flex; align-items: center; gap: 10px;
    font-size: 14px; color: var(--ink); height: 22px;
  }
  .contacts svg { width: 14px; height: 14px; fill: var(--red); flex: none; }
</style>
</head>
<body>

<section class="card card-front" aria-label="Business card front">
  <div class="brand">
    <span class="brand-square"></span>
    <span class="brand-name">Kestra Inspections</span>
  </div>
  <div class="front-band">
    <p>Also we do a lot of work using drones on natural gas pipelines</p>
  </div>
</section>

<section class="card card-back" aria-label="Business card back">
  <div class="brand">
    <span class="brand-square"></span>
    <span class="brand-name">Kestra Inspections</span>
  </div>
  <div class="person">
    <h1 class="person-name">Dana Marlow</h1>
    <p class="person-title">Managing Director</p>
  </div>
  <ul class="contacts">
    <li>
      <svg viewBox="0 0 24 24" aria-hidden="true"><path d="M6.6 10.8a15.1 15.1 0 0 0 6.6 6.6l2.2-2.2c.3-.3.7-.4 1-.2 1.1.4 2.3.6 3.6.6.6 0 1 .4 1 1V20c0 .6-.4 1-1 1A17 17 0 0 1 3 4c0-.6.4-1 1-1h3.5c.6 0 1 .4 1 1 0 1.3.2 2.5.6 3.6.1.3 0 .7-.2 1z"/></svg>
      1300 480 512
    </li>
    <li>
      <svg viewBox="0 0 24 24" aria-hidden="true"><path d="M12 2a10 10 0 1 0 0 20 10 10 0 0 0 0-20zm6.9 6h-3a15.7 15.7 0 0 0-1.3-3.9A8 8 0 0 1 18.9 8zM12 4c.8 1.2 1.5 2.5 1.9 4h-3.8c.4-1.5 1.1-2.8 1.9-4zM4.3 14a8.2 8.2 0 0 1 0-4h3.4a16 16 0 0 0 0 4zm.8 2h3a15.7 15.7 0 0 0 1.3 3.9A8 8 0 0 1 5.1 16zm3-8h-3a8 8 0 0 1 4.3-3.9C8.9 5.3 8.4 6.6 8.1 8zM12 20c-.8-1.2-1.5-2.5-1.9-4h3.8c-.4 1.5-1.1 2.8-1.9 4zm2.3-6H9.7a14.7 14.7 0 0 1 0-4h4.6a14.7 14.7 0 0 1 0 4zm.3 5.9c.6-1.2 1-2.5 1.3-3.9h3a8 8 0 0 1-4.3 3.9zm1.7-5.9a16 16 0 0 0 0-4h3.4a8.2 8.2 0 0 1 0 4z"/></svg>
      www.kestrafield.com
    </li>
    <li>
      <svg viewBox="0 0 24 24" aria-hidden="true"><path d="M2 5h20v14H2zm2 2v.5l8 5 8-5V7zm0 2.8V17h16V9.8l-8 5z"/></svg>
      dana.marlow@kestrafield.com
    </li>
  </ul>
</section>

</body>
</html>
```